Stage Design Company Business Card

We are looking to step up up our business card design for our team.

We are a Full service Design and Consultation company for Stage and TV with an emphasis in Theatrical Lighting.

We like our materials to be clean and modern with solid colors free of patterns and gradients. Our brand consists of 4 primary colors Purple, Black, Grey, and White. Provided is our Word Mark as well as our Symbol Logo.

We would like our cards to leave an impression beyond the information, show our attention to design and detail, and make our marks an easily recognized feature (together or apart) for our clients.

We need a warm approachable comfortable feel for some clients, and a professional flair for the board member type clients.

Attached are our brand elements, and our existing cards to give a sense of our style and a glipse at the information we provide on our cards.

Target Market(s)

broad client base from church leaders to high school teachers and architects.

Industry/Entity Type

Business

Contact Information for Business Card

We format our phone number with periods not parenthesis or dashes. Information will be edited for each of our team members, and team member specific cards are not part of this scope, but rather a template so to speak.

Font styles to use
Sans Serif

Colors
6b449b
ffffff
000000
333333
aaaaaa

Requirements
Must have
• Wordmark and logo mark present (does not need to exist on the same side of card)
• Brand Colors,
• Name, Phone, Email, Address.
• Unique choices that make someone stop and take a second look
Nice to have
• It would be nice to somehow convey what we DO, as our brand name does not lend itself to this, outside of an obvious tagline though.....
• social media if not crowded. all of our handles match (instagram, twitter, facebook)
Should not have
• "clipart"

```html
<!DOCTYPE html>
<html lang="en">
<head>
<meta charset="utf-8">
<title>Lumera Business Card</title>
<link href="https://fonts.googleapis.com/css2?family=Source+Sans+3:wght@400;600&display=swap" rel="stylesheet">
<style>
  :root {
    --backdrop: #000000;
    --card: #ffffff;
    --ink: #33206e;
    --text: #222222;
    --rule: #d6d6d6;
  }
  html, body {
    margin: 0;
    padding: 0;
    width: 1200px;
    height: 899px;
    overflow: hidden;
    background: var(--backdrop);
    font-family: "Source Sans 3", "Helvetica Neue", Arial, sans-serif;
  }
  .stage {
    position: relative;
    width: 1200px;
    height: 899px;
  }
  .card {
    position: absolute;
    top: 306px;
    width: 440px;
    height: 270px;
    background: var(--card);
    border-radius: 12px;
  }
  .card--front { left: 149px; }
  .card--back { left: 608px; }

  .brand {
    position: absolute;
    display: flex;
    flex-direction: column;
    align-items: center;
    color: var(--ink);
    font-weight: 600;
  }
  .brand__dot {
    border-radius: 50%;
    background: var(--ink);
  }
  .card--front .brand {
    left: 109px;
    top: 135px;
    transform: translate(-50%, -50%);
    gap: 14px;
    font-size: 20px;
    letter-spacing: 4px;
  }
  .card--front .brand__dot { width: 34px; height: 34px; }

  .divider {
    position: absolute;
    left: 204px;
    top: 66px;
    width: 1px;
    height: 150px;
    background: var(--rule);
  }

  .details {
    position: absolute;
    left: 238px;
    top: 70px;
    color: var(--text);
    font-size: 12.5px;
    line-height: 16px;
  }
  .details__name {
    margin: 0;
    color: var(--ink);
    font-size: 17.5px;
    font-weight: 600;
    line-height: 20px;
  }
  .details__role { margin: 0 0 12px; }
  .details__address { margin: 0 0 9px; font-style: normal; }
  .contact {
    list-style: none;
    margin: 0;
    padding: 0;
  }
  .contact li {
    display: flex;
    align-items: center;
    gap: 6px;
  }
  .contact svg { width: 9px; height: 9px; fill: var(--ink); flex: none; }

  .card--back .brand {
    left: 220px;
    top: 128px;
    transform: translate(-50%, -50%);
    gap: 26px;
    font-size: 24px;
    letter-spacing: 16px;
    padding-left: 16px;
  }
  .card--back .brand__dot { width: 48px; height: 48px; margin-right: 16px; }
</style>
</head>
<body>
<main class="stage">
  <section class="card card--front">
    <div class="brand">
      <span class="brand__dot"></span>
      <span class="brand__name">LUMERA</span>
    </div>
    <span class="divider"></span>
    <div class="details">
      <h1 class="details__name">Morgan Hale</h1>
      <p class="details__role">Managing Director</p>
      <address class="details__address">48 Footlight Lane<br>Bellmont, 204518.</address>
      <ul class="contact">
        <li>
          <svg viewBox="0 0 10 10" aria-hidden="true"><path d="M2 0.5 L3.6 2.6 L2.8 3.7 Q4 6 6.3 7.2 L7.4 6.4 L9.5 8 L8.3 9.5 Q4.5 9.4 0.5 1.7 Z"/></svg>
          <span>044-310 482 975</span>
        </li>
        <li>
          <svg viewBox="0 0 10 10" aria-hidden="true"><path d="M0.5 2 H9.5 V8.5 H0.5 Z M1.2 2.6 L5 5.6 L8.8 2.6 V3.3 L5 6.3 L1.2 3.3 Z" fill-rule="evenodd"/></svg>
          <span>hello@lumera.com</span>
        </li>
        <li>
          <svg viewBox="0 0 10 10" aria-hidden="true"><path d="M4.2 5.8 L5.8 4.2 M3.6 4.6 L1.8 6.4 A1.4 1.4 0 0 0 3.6 8.2 L5.4 6.4 M6.4 5.4 L8.2 3.6 A1.4 1.4 0 0 0 6.4 1.8 L4.6 3.6" stroke="#33206e" stroke-width="1.3" fill="none" stroke-linecap="round"/></svg>
          <span>www.lumerastage.com</span>
        </li>
      </ul>
    </div>
  </section>

  <section class="card card--back">
    <div class="brand">
      <span class="brand__dot"></span>
      <span class="brand__name">LUMERA</span>
    </div>
  </section>
</main>
</body>
</html>
```